Family business needs stationery redesign with new logo

Family owned company, established in 1987 wanting a brand 'refresh'. We are an electrical, refrigeration and construction company based in the Barkly Region Northern Territory, Australia. We have a new logo we would like to use which is uploaded along with our current letterhead and email signature. We are also dropping the word 'contractors' so please do not include this on any designs. Please note also, the 'orange' color used in our logo and designs should be Northern Territory red ochre which is as follows:

RGB (Hex): #C75B12
PantoneĀ® 159 C
CMYK: 1 / 74 / 100 / 7

We are needing our stationery redesigned using our new logo. Please include letterheads, business cards, envelopes, and email signatures.

We currently use our business letterheads for quotations, invoices, letters, HR matters, and internal memos.

We also need a separate simplified letterhead for internal paperwork such as employee leave forms, meeting agendas, and meeting minutes etc.

Reason: Needing more submissions of full package designs. We are wanting all our stationery, including business cards, letterheads, email signatures, envelopes, etc to be cohesive. We also require ALL the information, as supplied on our template letterhead, to be included on the new letterhead designs. including electrical license no.etc Thank you, R&W

Reason: needing more time as work has got in the way of looking over designs. A lot of designs not meeting the brief/criteria.

Industry/Entity Type

Business

Colors
0355a3
f37122

Requirements
Must have
• The 'orange' color used in the designs should be Northern Territory red ochre which is as follows:
• RGB (Hex): #C75B12
• PantoneĀ® 159 C
• CMYK: 1 / 74 / 100 / 7
• ***MUST INCLUDE ALL INFORMATION THAT IS ON OUR CURRENT LETTERHEAD***
Should not have
• Please do not include the word 'contractors'

```html
<!DOCTYPE html>
<html lang="en">
<head>
<meta charset="utf-8">
<title>R&amp;W Business Card</title>
<link rel="stylesheet" href="https://fonts.googleapis.com/css2?family=Arimo:wght@400;700&display=swap">
<style>
  :root {
    --backdrop: #e4e6ea;
    --card-face: #f2f3f5;
    --navy-deep: #18244f;
    --navy-mid: #26366c;
    --ochre: #c14a1e;
    --text-light: #dfe4ef;
    --brand-navy: #1f2b5c;
  }
  * { box-sizing: border-box; margin: 0; padding: 0; }
  html, body {
    width: 1200px;
    height: 969px;
    overflow: hidden;
    background: var(--backdrop);
    font-family: "Arimo", Arial, sans-serif;
  }
  .business-card {
    position: absolute;
    left: 100px;
    top: 200px;
    width: 1000px;
    height: 570px;
    border-radius: 24px;
    overflow: hidden;
    background: var(--card-face);
    box-shadow: 0 10px 30px rgba(20, 30, 60, 0.18);
  }
  .card-shapes {
    position: absolute;
    inset: 0;
    width: 100%;
    height: 100%;
  }
  .brand-name {
    position: absolute;
    left: 247px;
    top: 138px;
    transform: translate(-50%, -50%);
    font-weight: 700;
    font-size: 92px;
    letter-spacing: 2px;
    color: var(--brand-navy);
    line-height: 1;
  }
  .contact-block {
    position: absolute;
    right: 95px;
    top: 0;
    text-align: right;
    color: var(--text-light);
  }
  .contact-block p {
    position: absolute;
    right: 0;
    white-space: nowrap;
    line-height: 1;
  }
  .person-name {
    top: 203px;
    font-size: 31px;
    font-weight: 400;
    letter-spacing: 1.5px;
    color: var(--ochre);
  }
  .person-role { top: 246px; font-size: 27px; }
  .address-line { font-size: 25px; }
  .address-street { top: 305px; }
  .address-city { top: 340px; }
  .contact-line { font-size: 25px; }
  .contact-phone { top: 394px; }
  .contact-fax { top: 432px; }
  .contact-email { top: 470px; }
  .contact-web { top: 508px; }
  .contact-icon {
    position: absolute;
    left: 922px;
    width: 26px;
    height: 26px;
  }
  .icon-phone { top: 393px; }
  .icon-fax { top: 431px; }
  .icon-email { top: 469px; }
  .icon-web { top: 507px; }
</style>
</head>
<body>
  <div class="business-card">
    <svg class="card-shapes" viewBox="0 0 1000 570" preserveAspectRatio="none" aria-hidden="true">
      <defs>
        <linearGradient id="navyPanel" x1="0" y1="0" x2="1" y2="1">
          <stop offset="0" stop-color="#2a3a72"/>
          <stop offset="1" stop-color="#18244f"/>
        </linearGradient>
      </defs>
      <path d="M560,0 C595,250 410,480 195,570 L240,570 C430,470 630,260 640,0 Z" fill="var(--ochre)"/>
      <path d="M640,0 C630,260 430,470 240,570 L1000,570 L1000,0 Z" fill="url(#navyPanel)"/>
    </svg>

    <div class="brand-name">R&amp;W</div>

    <div class="contact-block">
      <p class="person-name">DANIEL HART</p>
      <p class="person-role">CEO/Founder</p>
      <p class="address-line address-street">214 Ironbark Road</p>
      <p class="address-line address-city">Tennant Creek, NT 0860</p>
      <p class="contact-line contact-phone">571 203 8846</p>
      <p class="contact-line contact-fax">573 118 4027</p>
      <p class="contact-line contact-email">hello@rwbuild.com</p>
      <p class="contact-line contact-web">www.rwbuild.com</p>
    </div>

    <svg class="contact-icon icon-phone" viewBox="0 0 24 24" aria-hidden="true">
      <path fill="var(--ochre)" d="M6.6 10.8c1.4 2.8 3.8 5.1 6.6 6.6l2.2-2.2c.3-.3.7-.4 1-.2 1.1.4 2.3.6 3.6.6.6 0 1 .4 1 1V20c0 .6-.4 1-1 1C10.6 21 3 13.4 3 4c0-.6.4-1 1-1h3.5c.6 0 1 .4 1 1 0 1.3.2 2.5.6 3.6.1.3 0 .7-.2 1l-2.3 2.2z"/>
    </svg>
    <svg class="contact-icon icon-fax" viewBox="0 0 24 24" aria-hidden="true">
      <rect x="7" y="3" width="10" height="5" fill="var(--ochre)"/>
      <rect x="3" y="9" width="18" height="8" rx="1.5" fill="var(--ochre)"/>
      <rect x="7" y="15" width="10" height="6" fill="var(--ochre)" stroke="#18244f" stroke-width="1.2"/>
    </svg>
    <svg class="contact-icon icon-email" viewBox="0 0 24 24" aria-hidden="true">
      <rect x="3" y="6" width="18" height="13" rx="1" fill="var(--ochre)"/>
      <path d="M3.5 6.5 12 13l8.5-6.5" fill="none" stroke="#18244f" stroke-width="1.5"/>
    </svg>
    <svg class="contact-icon icon-web" viewBox="0 0 24 24" aria-hidden="true">
      <circle cx="12" cy="12" r="9" fill="var(--ochre)"/>
      <path d="M3 12h18M12 3c3 3 3 15 0 18M12 3c-3 3-3 15 0 18" fill="none" stroke="#18244f" stroke-width="1.3"/>
    </svg>
  </div>
</body>
</html>
```